Executive Performance Review mapped on J-curve

I need to turn an executive company performance review into a visual infographic. The list of accomplishments is grouped into four calendar quarters. Each quarter needs a subtle representation of the season. The four quarters and associated list of accomplishments need to be mapped to a J-curve. - Spreadsheet with accomplishments attached (Marlowbend)- Sample image of a J-curve. You can google J-curve to see more images.- The title should be "Danica Ostrander Year in Review"

Target Market(s)

Board of Directors

Requirements
Nice to have
• This will be presented to a company founder that is an artist and customer experience expert. He is very visual so a nice visual representation of the data will be impactful. He also uses the phrase that you have to live with or work with someone for four seasons before you really know them. This is why I have the seasons mapped to the quarters. The Fall season motif should be gloomy and stormy.

```html
<!DOCTYPE html>
<html lang="en">
<head>
<meta charset="utf-8">
<title>Danica Ostrander Year in Review</title>
<link rel="stylesheet" href="https://fonts.googleapis.com/css2?family=Montserrat:wght@800&family=Source+Sans+3:wght@400;600;700&display=swap">
<style>
  :root{
    --ink:#1f1f1f;
    --summer-bg:#e9f5c1;
    --summer-bar:#a6d80c;
    --fall-bg:#f9dcc5;
    --fall-bar:#ee8a1e;
    --winter-bg:#f0fcfb;
    --winter-bar:#d9f7f3;
    --spring-bg:#eef7d6;
    --spring-bar:#c7e46a;
  }
  *{box-sizing:border-box;margin:0;padding:0}
  html,body{width:1200px;height:839px;overflow:hidden;background:#fff}
  body{position:relative;font-family:"Source Sans 3",sans-serif;color:var(--ink)}
  .title{position:absolute;top:84px;left:0;width:1200px;text-align:center;
    font-family:"Montserrat",sans-serif;font-weight:800;font-size:35px;letter-spacing:-0.3px;color:#2b2b2b}
  .season{position:absolute;top:150px;height:620px;width:257px}
  .season--summer{left:90px;background:var(--summer-bg)}
  .season--fall{left:347px;background:var(--fall-bg)}
  .season--winter{left:604px;background:var(--winter-bg)}
  .season--spring{left:861px;background:var(--spring-bg)}
  .jcurve{position:absolute;left:0;top:0}
  .tree{position:absolute;border-radius:48% 48% 20% 20%}
  .tree--summer{left:152px;top:598px;width:136px;height:150px;background:radial-gradient(circle at 50% 40%,#6fbf2a,#3f8f1c 60%,rgba(90,140,30,0) 72%)}
  .tree--fall{left:395px;top:566px;width:170px;height:180px;background:radial-gradient(circle at 50% 45%,#f14b1c,#f39a1a 50%,rgba(200,200,200,.4) 70%,rgba(0,0,0,0) 74%)}
  .tree--winter{left:656px;top:592px;width:152px;height:152px;background:radial-gradient(circle at 50% 45%,#ffffff,#dfe9ec 50%,rgba(120,80,60,.25) 68%,rgba(0,0,0,0) 72%)}
  .tree--spring{left:908px;top:554px;width:150px;height:178px;background:radial-gradient(circle at 50% 42%,#f7d6dc,#b8d86a 52%,rgba(120,80,40,.2) 68%,rgba(0,0,0,0) 72%)}
  .column{position:absolute;top:0;width:257px;height:839px}
  .column--summer{left:90px}.column--fall{left:347px}.column--winter{left:604px}.column--spring{left:861px}
  .section{position:absolute;left:0;width:257px}
  .section__head{height:14.5px;line-height:14.5px;padding-left:8px;font-weight:700;font-size:11.2px;letter-spacing:.1px}
  .column--summer .section__head{background:var(--summer-bar)}
  .column--fall .section__head{background:var(--fall-bar)}
  .column--winter .section__head{background:var(--winter-bar)}
  .column--spring .section__head{background:var(--spring-bar)}
  .section__list{list-style:none;padding:3px 12px 0 8px;font-size:11.2px;line-height:14px}
  .section__list li{margin-bottom:2.4px}
  .section__list li::before{content:"• "}
  .section__list--plain li{margin-bottom:0}
  .section__list--plain li::before{content:none}
  .season-label{position:absolute;top:753px;width:257px;text-align:center;font-weight:700;font-size:11.2px;letter-spacing:.1px}
</style>
</head>
<body>
  <h1 class="title">DANICA OSTRANDER YEAR IN REVIEW</h1>

  <div class="season season--summer"></div>
  <div class="season season--fall"></div>
  <div class="season season--winter"></div>
  <div class="season season--spring"></div>

  <svg class="jcurve" width="1200" height="839" viewBox="0 0 1200 839" aria-hidden="true">
    <defs>
      <linearGradient id="ground" x1="90" y1="0" x2="1118" y2="0" gradientUnits="userSpaceOnUse">
        <stop offset="0" stop-color="#9ccf2e"/>
        <stop offset="0.2" stop-color="#a8b82a"/>
        <stop offset="0.3" stop-color="#d48a22"/>
        <stop offset="0.47" stop-color="#e9a36a"/>
        <stop offset="0.6" stop-color="#c9eef0"/>
        <stop offset="0.78" stop-color="#d6ef9a"/>
        <stop offset="1" stop-color="#c8e55c"/>
      </linearGradient>
    </defs>
    <path d="M90,596 C180,610 280,665 348,672 S560,680 608,676 C720,668 820,640 900,600 C1000,540 1080,430 1118,272 L1118,770 L90,770 Z" fill="url(#ground)"/>
    <rect x="347" y="700" width="257" height="70" fill="#ee8a1e" opacity="0.55"/>
    <rect x="604" y="690" width="257" height="80" fill="#f0fcfb" opacity="0.7"/>
  </svg>

  <div class="tree tree--summer" role="img" aria-label="Leafy green summer tree on a sunny hill"></div>
  <div class="tree tree--fall" role="img" aria-label="Red and orange autumn tree under storm clouds, rain and lightning"></div>
  <div class="tree tree--winter" role="img" aria-label="Bare winter tree dusted with snow and snowflakes"></div>
  <div class="tree tree--spring" role="img" aria-label="Spring tree with pink blossoms and fresh leaves"></div>

  <div class="column column--summer">
    <section class="section" style="top:157px">
      <h2 class="section__head">TRANSITIONS</h2>
      <ul class="section__list">
        <li>RO Transition from Reid &amp; Tova</li>
        <li>Start CR Office Initiative</li>
        <li>Tactical Ops transition from Reid</li>
        <li>Formalize Exec Team</li>
      </ul>
    </section>
    <section class="section" style="top:251px">
      <h2 class="section__head">BIZ ARCHITECTURE</h2>
      <ul class="section__list">
        <li>Independent Financial Audit</li>
        <li>Organizational Audit - Structure</li>
        <li>Organizational Audit - People</li>
        <li>XF Framework - ESU</li>
        <li>Defined Utilization, Realization, Availability</li>
      </ul>
    </section>
    <section class="section" style="top:361px">
      <h2 class="section__head">STRATEGY</h2>
      <ul class="section__list">
        <li>Effective Strategy Meeting</li>
        <li>Strategic Themes 2018 - 2020: Stablize, Accel-<br>erate, Surge</li>
        <li>Business Drivers: Drive Revenue, Improve</li>
        <li>Corvane Experience, Increase Brand Awareness</li>
      </ul>
    </section>
    <section class="section" style="top:469px">
      <h2 class="section__head">SALES</h2>
      <ul class="section__list">
        <li>Talwick Account Transition</li>
        <li>QNL Account Transition</li>
        <li>2 year Managed Services Engagement Model</li>
      </ul>
    </section>
    <section class="section" style="top:546px">
      <h2 class="section__head">REVENUE / EBITA</h2>
      <ul class="section__list"><li>TBD</li></ul>
    </section>
    <p class="season-label">SUMMER: Q3 2018 - ASSESSMENT</p>
  </div>

  <div class="column column--fall">
    <section class="section" style="top:157px">
      <h2 class="section__head">BIZ ARCHITECTURE</h2>
      <ul class="section__list">
        <li>XF Framework - Functional Meetings &amp;</li>
        <li>Scrum of Scrums</li>
        <li>Structured Reorg</li>
        <li>Implemented Reorg</li>
        <li>Quarterly Org Iteration cadence</li>
        <li>Defined Key Hire Plan</li>
        <li>CR Office Operational</li>
        <li>Time Accountability</li>
        <li>Tools ReConfig</li>
        <li>Org Structure v1</li>
      </ul>
    </section>
    <section class="section" style="top:350px">
      <h2 class="section__head">STRATEGY</h2>
      <ul class="section__list"><li>Internal QBR Accountability</li></ul>
    </section>
    <section class="section" style="top:394px">
      <h2 class="section__head">SALES</h2>
      <ul class="section__list">
        <li>Brenmoor QBR</li>
        <li>Talwick QBR</li>
      </ul>
    </section>
    <section class="section" style="top:455px">
      <h2 class="section__head">REVENUE / EBITA</h2>
      <ul class="section__list"><li>TBD</li></ul>
    </section>
    <p class="season-label">FALL: Q4 2018 - STABLIZE</p>
  </div>

  <div class="column column--winter">
    <section class="section" style="top:158px">
      <h2 class="section__head">BIZ ARCHITECTURE</h2>
      <ul class="section__list">
        <li>XF Framework - Progress Demos</li>
        <li>Org Structure - COE's</li>
        <li>Stablize Accounting &amp; Finance</li>
        <li>Exec Hiring Process</li>
      </ul>
    </section>
    <section class="section" style="top:252px">
      <h2 class="section__head">KEY HIRES</h2>
      <ul class="section__list">
        <li>Controller</li>
        <li>Director CX</li>
      </ul>
    </section>
    <section class="section" style="top:313px">
      <h2 class="section__head">STRATEGY</h2>
      <ul class="section__list">
        <li>Founders removed from front line activity</li>
        <li>Vantry QBR - Goal Setting &amp; Tracking</li>
      </ul>
    </section>
    <section class="section" style="top:374px">
      <h2 class="section__head">SALES</h2>
      <ul class="section__list section__list--plain">
        <li>QNL QBR</li>
        <li>Talwick QBR</li>
      </ul>
    </section>
    <section class="section" style="top:430px">
      <h2 class="section__head">REVENUE / EBITA</h2>
      <ul class="section__list section__list--plain"><li>TBD</li></ul>
    </section>
    <p class="season-label">WINTER: Q1 2019 - STRATACTICAL</p>
  </div>

  <div class="column column--spring">
    <section class="section" style="top:157px">
      <h2 class="section__head">BIZ ARCHITECTURE</h2>
      <ul class="section__list">
        <li>Tiered Pricing Pre-Paid Engagement Model</li>
        <li>XF Framework - Ideation Board</li>
        <li>Consulting Levels &amp; Salary Bands</li>
        <li>Roles &amp; Responsibilities</li>
      </ul>
    </section>
    <section class="section" style="top:251px">
      <h2 class="section__head">KEY HIRES</h2>
      <ul class="section__list">
        <li>Interim HR</li>
        <li>Provisional Client Partner</li>
        <li>Acting Director 1</li>
        <li>Acting Director 2</li>
        <li>Client Partner 1</li>
        <li>Sales Exec 1</li>
      </ul>
    </section>
    <section class="section" style="top:378px">
      <h2 class="section__head">SALES</h2>
      <ul class="section__list">
        <li>Opened Brightpane Door</li>
        <li>Flipped focus from<br>operationaly run company to<br>sales/marketing driven org</li>
        <li>KRV Direct</li>
      </ul>
    </section>
    <section class="section" style="top:483px">
      <h2 class="section__head">REVENUE / EBITA</h2>
      <ul class="section__list"><li>TBD</li></ul>
    </section>
    <p class="season-label">SPRING: Q2 2019 - STRATEGIC</p>
  </div>
</body>
</html>
```